Medical Device Packaging Project 1 of 5

We are a medical device startup company needing packaging for a total of 5 device brands. This is posting 1 of 5 and the device name is "Vintaclear"

Vintaclear is an intraocular lens for use in cataract surgery. The target market is Chinese ophthalmologists. The box should be sophisticated and upmarket.

The company name is Brenmoor Optics, I have included the logo in the uploaded files section. You should include the logo on the box.

I have uploaded a sample lens boxes from other companies that demonstrate the information needed to be contained on the box in terms of address, warnings, symbols, etc.

I have also uploaded the blank dieline of the boxes

You are welcome and encouraged to also submit to projects 2, 3, 4, and 5 as well. The same rules and expectations apply.

Industry/Entity Type

It Company

Requirements
Should not have
• Should not have any images of an eye or any bionic/futuristic feel to the design
• Note that the calvisight box is for text reference only. You may use the lens image but the futuristic/bionic look is NOT what we are going for with this brand. It should be traditional upmarket medical device artwork.

```html
<!DOCTYPE html>
<html lang="en">
<head>
<meta charset="utf-8">
<title>Vintaclear – Hydrophobic Intraocular Lens Box Panels</title>
<link rel="stylesheet" href="https://fonts.googleapis.com/css2?family=Montserrat:wght@500;600;700&display=swap">
<style>
  :root {
    --stage: #e9eaec;
    --panel: #ffffff;
    --navy: #1d4f8c;
    --ink: #2b3f66;
    --sky: #7fd3ef;
    --sky-soft: #d6f1fb;
    --ice: #eef8fc;
    --steel: #b8bcc2;
    --steel-dark: #6e747b;
  }
  * { box-sizing: border-box; margin: 0; padding: 0; }
  html, body {
    width: 1200px; height: 782px; overflow: hidden;
    background: var(--stage);
    font-family: "Montserrat", sans-serif;
  }
  .box-panel {
    position: absolute; top: 176px;
    width: 530px; height: 430px;
    background: var(--panel);
    overflow: hidden;
    box-shadow: 0 10px 28px rgba(0,0,0,0.12);
  }
  .box-panel.back { left: 50px; }
  .box-panel.front { left: 620px; }

  .backdrop-pattern {
    position: absolute; inset: 0;
    background:
      radial-gradient(ellipse 55% 50% at 62% 80%, rgba(127,211,239,0.55), rgba(127,211,239,0) 70%),
      linear-gradient(180deg, var(--sky-soft) 0%, rgba(214,241,251,0) 12%),
      linear-gradient(160deg, var(--ice) 0%, var(--panel) 45%, var(--ice) 100%);
  }
  .top-band {
    position: absolute; left: 0; top: 0; width: 100%; height: 22px;
    background: linear-gradient(90deg, var(--sky-soft), #f5fbfe 60%, var(--sky-soft));
  }
  .brand-lockup {
    position: absolute; left: 30px; top: 64px;
    display: flex; align-items: center; gap: 9px;
  }
  .brand-dot {
    width: 12px; height: 12px; border-radius: 50%;
    background: var(--sky);
  }
  .brand-name {
    font-weight: 600; font-size: 18px; letter-spacing: 1.5px;
    color: var(--navy); text-transform: uppercase;
  }
  .product-type {
    position: absolute; right: 26px; top: 48px;
    font-weight: 600; font-size: 13px; line-height: 1.55;
    letter-spacing: 0.3px; text-align: right;
    color: var(--navy);
  }
  .lens-visual { position: absolute; }
  .back .lens-visual { right: 40px; top: 110px; width: 180px; height: 170px; }
  .front .lens-visual { right: 22px; top: 88px; width: 240px; height: 220px; }

  .warnings {
    position: absolute; left: 30px; top: 150px; width: 260px;
    font-weight: 500; font-size: 7.4px; line-height: 9.4px;
    color: var(--ink);
  }
  .warnings p + p { margin-top: 3px; }

  .symbols {
    position: absolute; right: 26px; top: 384px;
    display: flex; align-items: center; gap: 8px;
  }
  .sterile-mark {
    display: flex; border: 1px solid var(--ink);
    font-weight: 700; font-size: 6px; color: var(--ink);
  }
  .sterile-mark span { padding: 2px 3px; }
  .sterile-mark span + span { border-left: 1px solid var(--ink); }

  .product-name {
    position: absolute; left: 30px; top: 322px;
    font-weight: 700; font-size: 36px; letter-spacing: 6px;
    color: var(--navy); text-transform: uppercase;
  }
  .product-spec {
    position: absolute; left: 31px; top: 370px;
    font-weight: 600; font-size: 15px; letter-spacing: 0.4px;
    color: var(--navy);
  }
</style>
</head>
<body>
  <!-- Back panel -->
  <section class="box-panel back">
    <div class="backdrop-pattern" role="img" aria-label="Soft pale blue backdrop of translucent squares and circles"></div>
    <div class="top-band"></div>

    <div class="brand-lockup">
      <span class="brand-dot"></span>
      <span class="brand-name">Brenmoor Optics</span>
    </div>

    <h2 class="product-type">HYDROPHOBIC INTRAOCULAR LENS<br>ASPHERIC WITH 360° LENS</h2>

    <svg class="lens-visual" viewBox="0 0 180 170" role="img" aria-label="Illustration of an intraocular lens with two curved haptics">
      <defs>
        <radialGradient id="lensToneBack" cx="45%" cy="40%" r="60%">
          <stop offset="0%" stop-color="#e4e6e9"/>
          <stop offset="60%" stop-color="#b8bcc2"/>
          <stop offset="100%" stop-color="#6e747b"/>
        </radialGradient>
      </defs>
      <rect width="180" height="170" rx="14" fill="url(#lensToneBack)" opacity="0.35"/>
    </svg>

    <div class="warnings">
      <p>Contains one sterile intraocular lens<br>Do not use if the packaging is damaged<br>Do not resterilize</p>
      <p>Bevat één steriele intraoculaire lens<br>Niet gebruiken als de verpakking beschadigd is<br>Niet opnieuw steriliseren</p>
      <p>Contient une lentille intraoculaire stérile<br>Ne pas utiliser si l'emballage est endommagé<br>Ne pas restériliser</p>
      <p>Enthält eine sterile intraokulare Linse<br>Nicht verwenden, wenn die Verpackung beschädigt ist<br>Nicht resterilisieren</p>
      <p>Periéchei éna aposteiroméno endofthálmia fakó<br>Mi to chrisimopoieíte eán i syskevasía échei ypostei zimiá<br>Min to epanaposteirónete</p>
      <p>Contiene una lente intraoculare sterile<br>Non usare se la confezione è danneggiata<br>Non risterilizzare</p>
      <p>Contém uma lente intra-ocular esterilizada<br>Não use se a embalagem está danificada<br>Não reesterilize</p>
      <p>Contiene una lente intraocular estéril<br>No utilizar si el envase está dañado<br>No vuelva a esterilizar</p>
    </div>

    <div class="symbols">
      <div class="sterile-mark"><span>STERILE</span><span>EO</span></div>
      <svg width="14" height="13" viewBox="0 0 14 13" aria-label="Caution"><path d="M7 1 L13 12 H1 Z" fill="none" stroke="#2b3f66" stroke-width="1"/><path d="M7 5 V8.5 M7 10 V10.6" stroke="#2b3f66" stroke-width="1"/></svg>
      <svg width="13" height="13" viewBox="0 0 13 13" aria-label="Do not reuse"><circle cx="6.5" cy="6.5" r="5.7" fill="none" stroke="#2b3f66"/><path d="M2.5 10.5 L10.5 2.5" stroke="#2b3f66"/></svg>
      <svg width="13" height="13" viewBox="0 0 13 13" aria-label="Do not resterilize"><circle cx="6.5" cy="6.5" r="5.7" fill="none" stroke="#2b3f66"/><path d="M2.5 2.5 L10.5 10.5 M2.5 10.5 L10.5 2.5" stroke="#2b3f66"/></svg>
      <svg width="13" height="13" viewBox="0 0 13 13" aria-label="Do not use if package is damaged"><circle cx="6.5" cy="6.5" r="5.7" fill="none" stroke="#2b3f66"/><rect x="3.5" y="4" width="6" height="5" fill="none" stroke="#2b3f66" stroke-width="0.8"/></svg>
    </div>
  </section>

  <!-- Front panel -->
  <section class="box-panel front">
    <div class="backdrop-pattern" role="img" aria-label="Soft pale blue backdrop of translucent squares and circles"></div>
    <div class="top-band"></div>

    <div class="brand-lockup">
      <span class="brand-dot"></span>
      <span class="brand-name">Brenmoor Optics</span>
    </div>

    <h2 class="product-type">HYDROPHOBIC INTRAOCULAR LENS</h2>

    <svg class="lens-visual" viewBox="0 0 240 220" role="img" aria-label="Illustration of an intraocular lens with two curved haptics">
      <defs>
        <radialGradient id="lensToneFront" cx="55%" cy="40%" r="60%">
          <stop offset="0%" stop-color="#e4e6e9"/>
          <stop offset="60%" stop-color="#b8bcc2"/>
          <stop offset="100%" stop-color="#6e747b"/>
        </radialGradient>
      </defs>
      <rect width="240" height="220" rx="16" fill="url(#lensToneFront)" opacity="0.35"/>
    </svg>

    <h1 class="product-name">Vintaclear</h1>
    <p class="product-spec">ASPHERIC WITH 360° LENS</p>
  </section>
</body>
</html>
```